New Alcoholic Spiked Seltzer Line

We need a can design for a line of low calorie alcoholic seltzer. This product is a sparkling water and vodka drink with no sugar added in a slim 12 oz can.

This is a lighter, healthier, alternative to the sugary ready-to-drinks on the market. The product contains only 3 ingredients: Vodka, Water and Natural Flavors. It has only 100 calories but still has 5% alcohol, so you don't need to sacrifice alcohol to cut calories.

This product also does not contain any preservatives.

We want this design to communicate the following objectives to the consumer and in this order:

1. Appetizing product
2.Low calorie
3.Communicate the type of beverage (Spiked Seltzer)

The brand name of the product is VELKA.

The flavor of the product needed to be used for the design is Mango-Orange.

Comparable products are:

www.brindlefizzworks.example/
https://www.quorvabubbles.example
https://pelnavo.example/

The designs should not infringe or copy the creative directions of the products mentionned above. They are only given so that you can better understand the type of product we are developing.

Target Market(s)

Young Professional women between the ages of 25 and 44

Industry/Entity Type

Product

Colors

Designer to choose colors to be used in the design.

Requirements
Must have
• Design extendibility, meaning it can be adapted for other flavors.
• This is a new category in the market we are targeting, so consumers must easily be able to identify what type of product this is.

```html
<!DOCTYPE html>
<html lang="en">
<head>
<meta charset="utf-8">
<title>VELKA Spiked Seltzer – Mango-Orange Can Label</title>
<link href="https://fonts.googleapis.com/css2?family=Archivo:wght@400;600;800;900&family=Libre+Franklin:wght@400;700;900&display=swap" rel="stylesheet">
<style>
  :root {
    --label-white: #ffffff;
    --ink: #1b1b1b;
    --pink: #ec2f8e;
    --magenta: #d4237c;
    --coral: #f2635a;
    --orange: #f59a3b;
    --peach: #f7b66e;
    --icon-grey: #6b6b6b;
  }
  * { margin: 0; padding: 0; box-sizing: border-box; }
  html, body {
    width: 1200px; height: 2800px; overflow: hidden;
    background: var(--label-white);
  }
  .can-label {
    position: relative; width: 1200px; height: 2800px;
    background: var(--label-white);
    font-family: "Archivo", Arial, sans-serif; color: var(--ink);
    overflow: hidden;
  }
  .watercolor {
    position: absolute; left: -100px; width: 1400px;
    border-radius: 60px; opacity: 0.92;
  }
  .watercolor--top {
    top: 300px; height: 560px;
    transform: rotate(8deg);
    background: linear-gradient(100deg, var(--magenta) 0%, var(--pink) 35%, var(--coral) 62%, var(--orange) 85%, var(--peach) 100%);
  }
  .watercolor--bottom-pink {
    top: 1960px; height: 260px;
    transform: rotate(-12deg);
    background: linear-gradient(90deg, var(--pink) 0%, var(--magenta) 40%, var(--coral) 75%, var(--orange) 100%);
  }
  .watercolor--bottom-orange {
    top: 2320px; height: 300px;
    transform: rotate(-10deg);
    background: linear-gradient(90deg, var(--orange) 0%, var(--peach) 45%, var(--orange) 80%, var(--coral) 100%);
  }
  .label-copy {
    position: absolute; top: 860px; left: 0; width: 1200px;
    text-align: center; background: var(--label-white);
    padding: 20px 0 0;
  }
  .brand-name {
    font-weight: 800; font-size: 56px; letter-spacing: 6px; line-height: 1.1;
  }
  .product-type {
    font-weight: 800; font-size: 58px; letter-spacing: 2px; line-height: 1.2;
  }
  .description {
    font-family: "Libre Franklin", Arial, sans-serif; font-weight: 700;
    font-size: 34px; line-height: 1.25; margin: 20px auto 0; width: 680px;
  }
  .description + .description { margin-top: 40px; }
  .ingredients-title {
    margin-top: 56px; font-weight: 900; font-size: 32px; letter-spacing: 2px;
  }
  .ingredients {
    display: flex; justify-content: center; gap: 160px; margin-top: 40px;
  }
  .ingredient { width: 150px; display: flex; flex-direction: column; align-items: center; }
  .ingredient-box {
    width: 140px; height: 140px; border: 5px solid var(--ink);
    display: flex; align-items: center; justify-content: center;
  }
  .ingredient-name {
    font-family: "Libre Franklin", Arial, sans-serif; font-weight: 700;
    font-size: 32px; line-height: 1.1; margin-top: 20px;
  }
  .nutrition {
    position: absolute; top: 1720px; left: 352px; width: 480px;
    background: var(--label-white); border: 3px solid var(--ink);
    padding: 8px 12px 14px;
    font-family: "Libre Franklin", Arial, sans-serif; font-size: 19px; line-height: 1.35;
  }
  .nutrition-title { font-weight: 900; font-size: 58px; line-height: 1; letter-spacing: -1px; }
  .nutrition .row { display: flex; justify-content: space-between; border-top: 1.5px solid var(--ink); padding: 2px 0; }
  .nutrition .row--indent { padding-left: 26px; }
  .nutrition .rule-thick { border-top: 14px solid var(--ink); }
  .nutrition .rule-mid { border-top: 6px solid var(--ink); }
  .nutrition b { font-weight: 700; }
  .nutrition .footnote { border-top: 1.5px solid var(--ink); padding-top: 4px; font-size: 19px; line-height: 1.3; }
</style>
</head>
<body>
<main class="can-label">
  <div class="watercolor watercolor--top" role="img" aria-label="Pink to orange watercolor brush strokes in mango-orange tones"></div>
  <div class="watercolor watercolor--bottom-pink" role="img" aria-label="Pink watercolor brush stroke"></div>
  <div class="watercolor watercolor--bottom-orange" role="img" aria-label="Orange watercolor brush stroke"></div>

  <section class="label-copy">
    <h1 class="brand-name">VELKA</h1>
    <h2 class="product-type">Spiked Seltzer</h2>
    <p class="description">Juicy ripe mango meets bright sun-kissed orange in a crisp sparkling vodka seltzer with no sugar added.</p>
    <p class="description">Mango-Orange · 100 calories · 5% alc/vol</p>

    <h3 class="ingredients-title">MADE WITH 3 INGREDIENTS</h3>
    <div class="ingredients">
      <div class="ingredient">
        <div class="ingredient-box">
          <svg width="80" height="100" viewBox="0 0 80 100" aria-hidden="true">
            <path d="M40 6 C52 30 70 50 70 66 A30 30 0 0 1 10 66 C10 50 28 30 40 6 Z" fill="none" stroke="var(--ink)" stroke-width="7"/>
          </svg>
        </div>
        <span class="ingredient-name">Water</span>
      </div>
      <div class="ingredient">
        <div class="ingredient-box">
          <svg width="110" height="110" viewBox="0 0 110 110" role="img" aria-label="Fruit splash illustration">
            <circle cx="55" cy="55" r="44" fill="var(--icon-grey)"/>
          </svg>
        </div>
        <span class="ingredient-name">Natural Flavors</span>
      </div>
      <div class="ingredient">
        <div class="ingredient-box">
          <svg width="110" height="110" viewBox="0 0 110 110" aria-hidden="true">
            <path d="M10 14 H100 L55 60 Z" fill="var(--ink)"/>
            <rect x="52" y="58" width="6" height="38" fill="var(--ink)"/>
            <rect x="32" y="94" width="46" height="6" fill="var(--ink)"/>
            <circle cx="74" cy="28" r="6" fill="var(--label-white)"/>
          </svg>
        </div>
        <span class="ingredient-name">Vodka</span>
      </div>
    </div>
  </section>

  <section class="nutrition" aria-label="Nutrition Facts">
    <div class="nutrition-title">Nutrition Facts</div>
    <div>Serving Size 12 fl oz (355 mL)</div>
    <div class="row rule-thick">Amount Per Serving</div>
    <div class="row"><span>Calories 100</span><span>Calories from fat 0</span></div>
    <div class="row rule-mid"><span></span><b>% Daily Value*</b></div>
    <div class="row"><span><b>Total Fat</b> 0g</span><span>0%</span></div>
    <div class="row row--indent"><span>Saturated Fat 0g</span><span>0%</span></div>
    <div class="row row--indent"><span>Trans Fat 0g</span><span></span></div>
    <div class="row"><span><b>Cholesterol</b> 0mg</span><span>0%</span></div>
    <div class="row"><span><b>Sodium</b> 10mg</span><span>0%</span></div>
    <div class="row"><span><b>Total Carbohydrate</b> 2g</span><span>1%</span></div>
    <div class="row row--indent"><span>Dietary Fiber 0g</span><span></span></div>
    <div class="row row--indent"><span>Sugars 0g</span><span></span></div>
    <div class="row"><span><b>Protein</b> 0g</span><span></span></div>
    <div class="row rule-thick"><span>Vitamin A &nbsp;&nbsp;0% &nbsp;•</span><span>Vitamin C &nbsp;0%</span></div>
    <div class="row"><span>Calcium &nbsp;&nbsp;0% &nbsp;•&nbsp; Iron 0%</span><span></span></div>
    <p class="footnote">*Percent Daily Values are based on a 2,000 calorie diet. Your daily values may be higher or lower depending on your calorie needs.</p>
  </section>
</main>
</body>
</html>
```